Business Cards for Volmont Hayes, a law firm

We changed our firm's name from "Volmont & Hayes LLP" to "Volmont Hayes", we need to update our cards with a new design. We like the overall look of the back but the front side of the cards (see attached mockup) needs a refreshed look. I also attach our current logo so you can get rid of that LLP and &. We have a new address as well (not same as on mockup).

Target Market(s)

Clients of law firm

Industry/Entity Type

Law Firm

Contact Information for Business Card

Frontsides:

Lorenzo T. Volmont
Partner
Tel: (416) 555-0172 ext. 101
Fax: (647) 555-0139
Email: lvolmont@vhlegal.example

Simon P. Hayes
Partner
Tel: (416) 555-0172 ext. 102
Fax: (647) 555-0139
Email: simonhayes@vhlegal.example

Mark E. Dorsan
Barrister
Tel: (416) 555-0172 ext. 104
Fax: (647) 555-0139
Email: mdorsan@vhlegal.example

The back side should be crimson red (see mockup) with the logo (please update it to remove the & and the LLP, you can modify it a bit to make it tasteful if need be). Our new address is

82 Marlow Rd W, Suite 710
Toronto, ON M5K 0Z9

After our address, please also include our website www.vhlegal.example

Font styles to use
Sans Serif

Colors
ec2027
ffffff
000000

Requirements
Must have
• PLEASE NOTE: our firm's colour is more of a darker/crimson red, not a vibrant red.
• The front should have space for the lawyer's name, title, phone number (with extension), fax number, and email.
• If you're going to add those yourself, the info for the frontside is in the "Business Card Details" section (three lawyers that need their own cards).
Nice to have
• We like the backside of our current cards, just update it with our new address (one address now instead of 2), and a slightly modified logo (not a new logo altogether).
• The frontside should be refreshed with a better look (think minimalist, professional and modern), although still predominantly white-based background.
Should not have
• No scales of justice or other cheesy lawyer stereotype symbols! :-)

```html
<!DOCTYPE html>
<html lang="en">
<head>
<meta charset="utf-8">
<title>Volmont Hayes – Business Cards</title>
<link rel="stylesheet" href="https://fonts.googleapis.com/css2?family=Montserrat:wght@300&family=Rubik:wght@400;500;700&display=swap">
<style>
  :root {
    --page: #f4f4f4;
    --crimson: #c21d14;
    --crimson-dark: #8a1510;
    --white: #ffffff;
    --ink: #1a1a1a;
    --rule: #dcdcdc;
    --ghost: #f1f1f1;
  }
  * { box-sizing: border-box; margin: 0; padding: 0; }
  html, body { width: 1200px; height: 1098px; overflow: hidden; background: var(--page); }
  body { position: relative; font-family: "Rubik", sans-serif; color: var(--ink); }

  .sheet-heading {
    position: absolute; left: 54px; top: 26px;
    font-family: "Montserrat", sans-serif; font-weight: 300;
    font-size: 31px; line-height: 39px; letter-spacing: 2px;
    color: var(--ink); text-transform: uppercase;
  }

  .card { position: absolute; overflow: hidden; }

  /* Back side */
  .card-back {
    left: 53px; width: 537px; height: 268px;
    background: var(--crimson);
  }
  .card-back .brand-mark {
    position: absolute; left: 50%; top: 30px; width: 76px; height: 76px;
    margin-left: -38px; border: 7px solid var(--white); border-radius: 50%;
  }
  .card-back .brand-name {
    position: absolute; left: 0; right: 0; top: 122px; text-align: center;
    font-size: 30px; font-weight: 700; color: var(--white); letter-spacing: 0.2px;
  }
  .card-back .info-band {
    position: absolute; left: 0; right: 0; top: 192px; bottom: 0;
    border-top: 2px solid var(--crimson-dark);
  }
  .card-back .address {
    position: absolute; left: 24px; top: 20px;
    display: flex; gap: 7px; align-items: flex-start;
    color: var(--white); font-size: 11.5px; font-weight: 500; line-height: 15px;
  }
  .card-back .address svg { margin-top: 1px; flex: none; }
  .card-back .website {
    position: absolute; right: 42px; top: 28px;
    color: var(--white); font-size: 12px; font-weight: 500; letter-spacing: 0.5px;
  }

  /* Front side */
  .card-front {
    left: 620px; width: 527px; height: 270px;
    background: var(--white);
    box-shadow: 0 3px 8px rgba(0,0,0,0.18);
  }
  .card-front .ghost-mark {
    position: absolute; left: 8px; top: 58px; width: 260px; height: 260px;
    border: 14px solid var(--ghost); border-radius: 50%;
  }
  .card-front .brand-mark {
    position: absolute; left: 106px; top: 90px; width: 42px; height: 42px;
    border: 5px solid var(--crimson); border-radius: 50%;
  }
  .card-front .brand-name {
    position: absolute; left: 27px; width: 200px; top: 154px; text-align: center;
    font-size: 17px; font-weight: 700; color: var(--crimson);
  }
  .card-front .divider {
    position: absolute; left: 238px; top: 44px; width: 1px; height: 183px;
    background: var(--rule);
  }
  .card-front .contact { position: absolute; left: 298px; top: 82px; }
  .contact .person-name { font-size: 14.5px; font-weight: 700; letter-spacing: 0.6px; }
  .contact .person-title { font-size: 12px; color: var(--crimson); letter-spacing: 0.4px; margin-top: 1px; }
  .contact .details { list-style: none; margin-top: 26px; }
  .contact .details li {
    display: flex; align-items: center; gap: 7px;
    font-size: 12px; line-height: 16.5px; letter-spacing: 0.6px;
  }
  .contact .details svg { flex: none; }

  .row-1 { top: 178px; }
  .row-2 { top: 469px; }
  .row-3 { top: 762px; }
</style>
</head>
<body>

<h1 class="sheet-heading">+ Logo<br>+ Buissness cards<br>(in editable file and different formats)</h1>

<!-- Row 1 -->
<section class="card card-back row-1">
  <div class="brand-mark"></div>
  <div class="brand-name">Volmont Hayes</div>
  <div class="info-band">
    <div class="address">
      <svg width="11" height="15" viewBox="0 0 11 15"><path d="M5.5 0A5.5 5.5 0 0 0 0 5.5C0 9.5 5.5 15 5.5 15S11 9.5 11 5.5A5.5 5.5 0 0 0 5.5 0zm0 7.6a2.1 2.1 0 1 1 0-4.2 2.1 2.1 0 0 1 0 4.2z" fill="#fff"/></svg>
      <span>82 Marlow Rd W, Suite 710<br>Toronto, ON M5K 0Z9</span>
    </div>
    <div class="website">www.vhlegal.example</div>
  </div>
</section>
<section class="card card-front row-1">
  <div class="ghost-mark"></div>
  <div class="brand-mark"></div>
  <div class="brand-name">Volmont Hayes</div>
  <div class="divider"></div>
  <div class="contact">
    <div class="person-name">Lorenzo T. Volmont</div>
    <div class="person-title">Partner</div>
    <ul class="details">
      <li><svg width="11" height="11" viewBox="0 0 11 11"><path d="M2.2 0.5l1.8 2.2-1 1.3c.7 1.6 2 2.9 3.6 3.6l1.3-1 2.2 1.8-.9 1.9C4.6 10.3 0.7 6.4 0.3 1.4z" fill="#c21d14"/></svg>(416) 555-0172 ext. 101</li>
      <li><svg width="11" height="11" viewBox="0 0 11 11"><rect x="2.5" y="0.5" width="6" height="3" fill="#c21d14"/><rect x="0.5" y="4" width="10" height="5" rx="1" fill="#c21d14"/><rect x="2.5" y="7.5" width="6" height="3" fill="#c21d14"/></svg>(647) 555-0139</li>
      <li><svg width="11" height="9" viewBox="0 0 11 9"><rect x="0" y="0.5" width="11" height="8" rx="1" fill="#c21d14"/><path d="M0.8 1.4l4.7 3.6 4.7-3.6" stroke="#fff" stroke-width="1.1" fill="none"/></svg>lvolmont@vhlegal.example</li>
    </ul>
  </div>
</section>

<!-- Row 2 -->
<section class="card card-back row-2">
  <div class="brand-mark"></div>
  <div class="brand-name">Volmont Hayes</div>
  <div class="info-band">
    <div class="address">
      <svg width="11" height="15" viewBox="0 0 11 15"><path d="M5.5 0A5.5 5.5 0 0 0 0 5.5C0 9.5 5.5 15 5.5 15S11 9.5 11 5.5A5.5 5.5 0 0 0 5.5 0zm0 7.6a2.1 2.1 0 1 1 0-4.2 2.1 2.1 0 0 1 0 4.2z" fill="#fff"/></svg>
      <span>82 Marlow Rd W, Suite 710<br>Toronto, ON M5K 0Z9</span>
    </div>
    <div class="website">www.vhlegal.example</div>
  </div>
</section>
<section class="card card-front row-2">
  <div class="ghost-mark"></div>
  <div class="brand-mark"></div>
  <div class="brand-name">Volmont Hayes</div>
  <div class="divider"></div>
  <div class="contact">
    <div class="person-name">Simon P. Hayes</div>
    <div class="person-title">Partner</div>
    <ul class="details">
      <li><svg width="11" height="11" viewBox="0 0 11 11"><path d="M2.2 0.5l1.8 2.2-1 1.3c.7 1.6 2 2.9 3.6 3.6l1.3-1 2.2 1.8-.9 1.9C4.6 10.3 0.7 6.4 0.3 1.4z" fill="#c21d14"/></svg>(416) 555-0172 ext. 102</li>
      <li><svg width="11" height="11" viewBox="0 0 11 11"><rect x="2.5" y="0.5" width="6" height="3" fill="#c21d14"/><rect x="0.5" y="4" width="10" height="5" rx="1" fill="#c21d14"/><rect x="2.5" y="7.5" width="6" height="3" fill="#c21d14"/></svg>(647) 555-0139</li>
      <li><svg width="11" height="9" viewBox="0 0 11 9"><rect x="0" y="0.5" width="11" height="8" rx="1" fill="#c21d14"/><path d="M0.8 1.4l4.7 3.6 4.7-3.6" stroke="#fff" stroke-width="1.1" fill="none"/></svg>simonhayes@vhlegal.example</li>
    </ul>
  </div>
</section>

<!-- Row 3 -->
<section class="card card-back row-3">
  <div class="brand-mark"></div>
  <div class="brand-name">Volmont Hayes</div>
  <div class="info-band">
    <div class="address">
      <svg width="11" height="15" viewBox="0 0 11 15"><path d="M5.5 0A5.5 5.5 0 0 0 0 5.5C0 9.5 5.5 15 5.5 15S11 9.5 11 5.5A5.5 5.5 0 0 0 5.5 0zm0 7.6a2.1 2.1 0 1 1 0-4.2 2.1 2.1 0 0 1 0 4.2z" fill="#fff"/></svg>
      <span>82 Marlow Rd W, Suite 710<br>Toronto, ON M5K 0Z9</span>
    </div>
    <div class="website">www.vhlegal.example</div>
  </div>
</section>
<section class="card card-front row-3">
  <div class="ghost-mark"></div>
  <div class="brand-mark"></div>
  <div class="brand-name">Volmont Hayes</div>
  <div class="divider"></div>
  <div class="contact">
    <div class="person-name">Mark E. Dorsan</div>
    <div class="person-title">Barrister</div>
    <ul class="details">
      <li><svg width="11" height="11" viewBox="0 0 11 11"><path d="M2.2 0.5l1.8 2.2-1 1.3c.7 1.6 2 2.9 3.6 3.6l1.3-1 2.2 1.8-.9 1.9C4.6 10.3 0.7 6.4 0.3 1.4z" fill="#c21d14"/></svg>(416) 555-0172 ext. 104</li>
      <li><svg width="11" height="11" viewBox="0 0 11 11"><rect x="2.5" y="0.5" width="6" height="3" fill="#c21d14"/><rect x="0.5" y="4" width="10" height="5" rx="1" fill="#c21d14"/><rect x="2.5" y="7.5" width="6" height="3" fill="#c21d14"/></svg>(647) 555-0139</li>
      <li><svg width="11" height="9" viewBox="0 0 11 9"><rect x="0" y="0.5" width="11" height="8" rx="1" fill="#c21d14"/><path d="M0.8 1.4l4.7 3.6 4.7-3.6" stroke="#fff" stroke-width="1.1" fill="none"/></svg>mdorsan@vhlegal.example</li>
    </ul>
  </div>
</section>

</body>
</html>
```